Elegant and modern Wedding Photography brochure

My existing brochure (attached) needs a major facelift. This is one of the main selling tools - it gets emailed to my clients when they make an equiry on what packages i offer and it is printed out and walked through at our first meeting. This brochure is as critical as my website - it needs to sing!

I'm looking for an eye-catching design that says:
Elegant
Modern
Clean
Crisp
Not cutesy or lovey-dovey thanks - we are more sophisticated and professional than that.

Update images to some of the latest weddings I've shot also. Let me know files and resolution you need. I've enabled right-click to download images on my site for a limited time. Please note that I retain copyright and will pursue any breeches.

Http://www.sarahkelbrin.com/Melbourne-wedding-photography
Updates

Thanks for all of your designs! Will take a few days to decide.

Target Market(s)

Australian Women aged 24-44

Industry/Entity Type

Wedding

Font styles to use
Other font styles liked:
• Century Gothic

Requirements
Must have
• Easy to print - does not have to be 6 A4 pages like the existing brochure
Nice to have
• Some full page images - The photos are supposed to be the hero here :-)
Should not have
• Not cutesy or lovey-dovey thanks - we are more sophisticated and professional than that.

No black backgrounds, I prefer a white thanks

No images in organic shaped boxes (like the rectangles in the logo - no thanks).
Keep the lines straight and sharp

```html
<!DOCTYPE html>
<html lang="en">
<head>
<meta charset="utf-8">
<title>Sarah Kelbrin Wedding Photography</title>
<link href="https://fonts.googleapis.com/css2?family=Questrial&display=swap" rel="stylesheet">
<style>
  :root {
    --white: #ffffff;
    --plum: #7b2d86;
    --blush: #f0a7cf;
    --band-text: #f6d9ee;
    --body-grey: #6f6f6f;
    --photo-pale: #ececec;
    --photo-light: #d9d9d9;
    --photo-mid: #a8a8a8;
    --photo-deep: #4a4a4a;
    --photo-shadow: #2a2a2a;
  }
  html, body {
    margin: 0;
    padding: 0;
    width: 1200px;
    height: 851px;
    overflow: hidden;
    background: var(--white);
  }
  .page {
    position: relative;
    width: 1200px;
    height: 851px;
    background: var(--white);
    font-family: "Questrial", "Century Gothic", sans-serif;
  }
  .hero-photo {
    position: absolute;
    left: 0;
    top: 0;
    width: 561px;
    height: 851px;
    background:
      radial-gradient(ellipse 70% 22% at 45% 18%, rgba(42, 42, 42, 0.55) 0%, rgba(42, 42, 42, 0) 100%),
      radial-gradient(ellipse 80% 30% at 35% 68%, rgba(250, 250, 250, 0.55) 0%, rgba(250, 250, 250, 0) 100%),
      linear-gradient(180deg, var(--photo-pale) 0%, var(--photo-light) 45%, var(--photo-mid) 72%, var(--photo-deep) 90%, var(--photo-shadow) 100%);
  }
  .intro {
    position: absolute;
    left: 640px;
    top: 110px;
    width: 484px;
    text-align: center;
  }
  .intro-title {
    margin: 0 0 30px;
    font-weight: 400;
    font-size: 31px;
    line-height: 35px;
    color: var(--blush);
  }
  .intro-copy {
    margin: 0 auto 20px;
    width: 372px;
    font-size: 15px;
    line-height: 20.5px;
    color: var(--body-grey);
  }
  .contact-band {
    position: absolute;
    left: 561px;
    top: 511px;
    width: 639px;
    height: 185px;
    background: var(--plum);
  }
  .contact-list {
    margin: 0;
    padding: 18px 0 0;
    list-style: none;
    position: absolute;
    left: 78px;
    width: 484px;
    text-align: center;
    color: var(--band-text);
  }
  .contact-list li {
    font-size: 27px;
    line-height: 34px;
  }
  .contact-list .contact-address {
    font-size: 25px;
  }
  .brand {
    position: absolute;
    left: 758px;
    top: 730px;
    display: flex;
    align-items: center;
    gap: 12px;
  }
  .brand-mark {
    width: 50px;
    height: 50px;
    display: block;
  }
  .brand-name {
    font-size: 33px;
    line-height: 50px;
    color: var(--plum);
  }
</style>
</head>
<body>
<main class="page">
  <div class="hero-photo" role="img" aria-label="Black and white photograph of bridal shoes, a perfume bottle and a ring beneath a crystal-draped lamp on a mirrored table"></div>

  <section class="intro">
    <h1 class="intro-title">How do you want to remember<br>your special day?</h1>
    <p class="intro-copy">Elegant, stunning, fuss-free photography that doesn't cost the earth will capture those memories for a lifetime!</p>
    <p class="intro-copy">Wedding photography packages start from $1650 and are fully inclusive of fun-filled creative &amp; journalistic coverage, digital negatives and professionally edited album.</p>
    <p class="intro-copy">Contact Sarah today to arrange an informal catch-up, discuss your requirements and find out more about the early booking bonus!</p>
  </section>

  <section class="contact-band">
    <ul class="contact-list">
      <li class="contact-address">Harlow Lane, Seddon, VIC, 3011</li>
      <li>www.sarahkelbrin.com</li>
      <li>Email: sarah@sarahkelbrin.com</li>
      <li>Mobile: 0400 582 106</li>
    </ul>
  </section>

  <div class="brand">
    <svg class="brand-mark" viewBox="0 0 50 50" aria-hidden="true">
      <rect x="4" y="4" width="42" height="42" fill="none" stroke="#7b2d86" stroke-width="3"/>
    </svg>
    <span class="brand-name">Sarah Kelbrin</span>
  </div>
</main>
</body>
</html>
```